Ward Compass Business Card Design*

We need a business card design for our company Ward Compass. Our company is specialized in providing online consulting services regarding medical institutions, hospitals and doctors. We work with patients worldwide looking to choose between healthcare providers. We have a website you may use as a reference, where we list doctors and clinics worldwide. So we target Medical providers as well as patients worldwide.
Target Market(s)
Medical Providers and patients around the world
Industry/Entity Type
Medical
Contact Information for Business Card
Salwa Kettani
CEO
+90 612 348 2175
info@wardcompass.example
www.wardcompass.example
14 Annakhil 7 H.R.B. Rabat, Morocco
Requirements
Must have
- Company logo/name on one full side, personal info and smaller logo and company name on the other side.
Nice to have
- Smart and elegant design

```html
<!DOCTYPE html>
<html lang="en">
<head>
<meta charset="utf-8">
<title>Ward Compass Business Card</title>
<link href="https://fonts.googleapis.com/css2?family=Montserrat:wght@500;700&family=Lato:wght@400&display=swap" rel="stylesheet">
<style>
  :root {
    --stage: #e6e7e9;
    --paper: #fbf7f7;
    --blue-deep: #2f6fb5;
    --blue-sky: #2ba3da;
    --ink: #1d1d1f;
    --rule: #c9c9cc;
    --white: #ffffff;
  }
  * { box-sizing: border-box; margin: 0; padding: 0; }
  html, body { width: 1200px; height: 782px; overflow: hidden; }
  body {
    background: var(--stage);
    position: relative;
    font-family: "Lato", sans-serif;
  }
  .card {
    position: absolute;
    top: 242px;
    width: 520px;
    height: 298px;
    box-shadow: 0 6px 18px rgba(0,0,0,.18);
    overflow: hidden;
  }
  .card--back { left: 50px; }
  .card--front { left: 630px; background: var(--paper); }

  .back-field {
    position: absolute; inset: 0;
    background: linear-gradient(160deg, var(--blue-sky) 0%, #2f8fd0 50%, var(--blue-deep) 100%);
  }
  .back-name {
    position: absolute; inset: 0;
    display: flex; align-items: center; justify-content: center; gap: 10px;
    font-family: "Montserrat", sans-serif;
    font-weight: 700;
    font-size: 22px;
    letter-spacing: 1px;
    text-transform: uppercase;
    color: var(--white);
  }
  .back-name .dot {
    width: 18px; height: 18px; border-radius: 50%;
    background: var(--white);
  }

  .brand {
    position: absolute;
    left: 30px; top: 118px;
    display: flex; align-items: center; gap: 10px;
    font-family: "Montserrat", sans-serif;
    font-weight: 700;
    font-size: 19px;
    letter-spacing: .5px;
    text-transform: uppercase;
    color: var(--blue-deep);
  }
  .brand .dot {
    width: 30px; height: 30px; border-radius: 50%;
    background: var(--blue-deep);
  }
  .divider {
    position: absolute;
    left: 268px; top: 70px;
    width: 1px; height: 130px;
    background: var(--rule);
  }
  .person {
    position: absolute;
    left: 292px; top: 78px;
  }
  .person__name {
    font-family: "Montserrat", sans-serif;
    font-size: 19px;
    text-transform: uppercase;
    line-height: 1;
  }
  .person__given { font-weight: 700; color: var(--blue-deep); }
  .person__family { font-weight: 500; color: var(--blue-sky); }
  .person__role {
    font-size: 13px; color: var(--ink);
    margin-top: 3px; letter-spacing: .5px;
  }
  .contacts {
    list-style: none;
    margin-top: 22px;
  }
  .contacts li {
    display: flex; align-items: center; gap: 8px;
    font-size: 14px; color: var(--ink);
    line-height: 21px;
  }
  .contacts svg { width: 12px; height: 12px; flex: none; }
  .bands {
    position: absolute; left: 0; bottom: 0;
    width: 520px; height: 34px;
  }
</style>
</head>
<body>

  <section class="card card--back" aria-label="Card back">
    <div class="back-field" role="img" aria-label="Blue gradient field with a faint repeated brand pattern"></div>
    <div class="back-name"><span class="dot"></span>Ward Compass</div>
  </section>

  <section class="card card--front" aria-label="Card front">
    <div class="brand"><span class="dot"></span>Ward Compass</div>
    <div class="divider"></div>

    <div class="person">
      <p class="person__name"><span class="person__given">Salwa</span> <span class="person__family">Kettani</span></p>
      <p class="person__role">CEO</p>
      <ul class="contacts">
        <li>
          <svg viewBox="0 0 12 12" aria-hidden="true"><rect width="12" height="12" rx="2" fill="#2ba3da"/><path d="M3.4 2.8c.4 2.8 2.4 4.9 5.2 5.6l.8-1.2-1.4-.8-.7.7C6 6.5 5.4 5.9 4.8 4.6l.7-.7-.8-1.4z" fill="#fff"/></svg>
          +90 612 348 2175
        </li>
        <li>
          <svg viewBox="0 0 12 12" aria-hidden="true"><rect width="12" height="12" rx="2" fill="#2ba3da"/><rect x="2.5" y="3.5" width="7" height="5" fill="none" stroke="#fff" stroke-width="1"/><path d="M2.5 3.5 6 6.3 9.5 3.5" fill="none" stroke="#fff" stroke-width="1"/></svg>
          info@wardcompass.example
        </li>
        <li>
          <svg viewBox="0 0 12 12" aria-hidden="true"><circle cx="6" cy="6" r="6" fill="#2ba3da"/><circle cx="6" cy="6" r="3.6" fill="none" stroke="#fff" stroke-width=".9"/><path d="M2.4 6h7.2M6 2.4c-1.6 2-1.6 5.2 0 7.2M6 2.4c1.6 2 1.6 5.2 0 7.2" fill="none" stroke="#fff" stroke-width=".8"/></svg>
          www.wardcompass.example
        </li>
      </ul>
    </div>

    <svg class="bands" viewBox="0 0 520 34" aria-hidden="true">
      <polygon points="0,6 300,6 300,18 0,18" fill="var(--blue-deep)"/>
      <polygon points="308,10 520,10 520,34 296,34" fill="var(--blue-sky)"/>
    </svg>
  </section>

</body>
</html>
```